Business card for event manager / organizer "waiter service"

Draft of a new valuable business card for my company.
Events, personnel service providers, festivals

```html
<!DOCTYPE html>
<html lang="de">
<head>
<meta charset="utf-8">
<title>Tafelrunde Eventservice – Visitenkarte</title>
<link rel="stylesheet" href="https://fonts.googleapis.com/css2?family=Montserrat:wght@600;800&family=Poppins:wght@300;400;500&display=swap">
<style>
  :root {
    --stage: #3b3b3d;
    --card: #272326;
    --orange: #ef8220;
    --white: #ffffff;
    --muted: #d9d9d9;
  }
  * { box-sizing: border-box; margin: 0; padding: 0; }
  html, body { width: 1200px; height: 900px; overflow: hidden; }
  body {
    background: var(--stage);
    font-family: "Poppins", sans-serif;
    color: var(--white);
    position: relative;
  }
  .card {
    position: absolute;
    left: 250px;
    width: 700px;
    height: 400px;
    background: var(--card);
    border-radius: 22px;
    overflow: hidden;
    box-shadow: 0 10px 30px rgba(0,0,0,.45);
  }
  .card--front { top: 30px; }
  .card--back { top: 470px; }

  /* Brand lockup */
  .brand {
    position: absolute;
    display: flex;
    align-items: center;
    gap: 18px;
  }
  .brand__mark {
    background: var(--orange);
    flex: none;
  }
  .brand__name {
    font-family: "Montserrat", sans-serif;
    font-weight: 800;
    color: var(--white);
    text-transform: uppercase;
    line-height: 1.05;
  }
  .card--front .brand { left: 70px; top: 70px; }
  .card--front .brand__mark { width: 110px; height: 110px; }
  .card--front .brand__name { font-size: 44px; }
  .tagline {
    position: absolute;
    font-weight: 300;
    color: var(--white);
    white-space: nowrap;
  }
  .card--front .tagline { left: 198px; top: 190px; font-size: 19px; }

  /* Front */
  .pill {
    position: absolute;
    left: 205px;
    top: 238px;
    padding: 10px 30px;
    border: 3px solid var(--orange);
    border-radius: 40px;
    font-family: "Montserrat", sans-serif;
    font-weight: 800;
    font-size: 30px;
    color: var(--orange);
    letter-spacing: 1px;
  }
  .services {
    position: absolute;
    left: 70px;
    top: 330px;
    font-size: 22px;
    font-weight: 400;
    display: flex;
    align-items: center;
    gap: 10px;
  }
  .services__dot {
    width: 10px; height: 10px; border-radius: 50%;
    background: var(--orange);
    display: inline-block;
  }

  /* Back */
  .card--back .brand { left: 300px; top: 28px; gap: 10px; }
  .card--back .brand__mark { width: 44px; height: 44px; }
  .card--back .brand__name { font-size: 17px; }
  .card--back .tagline { left: 354px; top: 80px; font-size: 9px; }
  .portrait {
    position: absolute;
    left: 70px;
    top: 110px;
    width: 200px;
    height: 200px;
    border-radius: 50%;
    border: 3px solid var(--orange);
    background: radial-gradient(circle at 50% 40%, #8a8a8c 0%, #4d4d50 60%, #2f2f31 100%);
  }
  .person {
    position: absolute;
    left: 310px;
    top: 112px;
  }
  .person__name {
    font-family: "Montserrat", sans-serif;
    font-weight: 800;
    font-size: 30px;
    color: var(--orange);
  }
  .person__role {
    font-size: 15px;
    color: var(--muted);
    margin-top: -2px;
  }
  .contact {
    list-style: none;
    margin-top: 14px;
  }
  .contact__item {
    display: flex;
    align-items: center;
    gap: 10px;
    font-size: 15px;
    line-height: 24px;
  }
  .contact__icon { width: 14px; height: 14px; flex: none; fill: var(--orange); }
  .band {
    position: absolute;
    left: 0; bottom: 0;
    width: 700px; height: 40px;
  }
</style>
</head>
<body>

<section class="card card--front">
  <div class="brand">
    <span class="brand__mark"></span>
    <span class="brand__name">Tafelrunde<br>Eventservice</span>
  </div>
  <p class="tagline">…weil jedes Fest gute Gastgeber braucht!</p>
  <div class="pill">WAITER SERVICE</div>
  <p class="services">
    Events, <span class="services__dot"></span> personnel service providers, <span class="services__dot"></span> festivals
  </p>
</section>

<section class="card card--back">
  <div class="brand">
    <span class="brand__mark"></span>
    <span class="brand__name">Tafelrunde<br>Eventservice</span>
  </div>
  <p class="tagline">…weil jedes Fest gute Gastgeber braucht!</p>

  <div class="portrait" role="img" aria-label="Portraitfoto des Inhabers in Weste vor grauem Hintergrund"></div>

  <div class="person">
    <h1 class="person__name">Marlo Hennecke</h1>
    <p class="person__role">Inhaber</p>
    <ul class="contact">
      <li class="contact__item">
        <svg class="contact__icon" viewBox="0 0 24 24"><path d="M6.6 10.8a15 15 0 0 0 6.6 6.6l2.2-2.2a1 1 0 0 1 1-.25 11.4 11.4 0 0 0 3.6.57 1 1 0 0 1 1 1V20a1 1 0 0 1-1 1A17 17 0 0 1 3 4a1 1 0 0 1 1-1h3.5a1 1 0 0 1 1 1c0 1.25.2 2.450.57 3.57a1 1 0 0 1-.25 1z"/></svg>
        02361 555 01 23
      </li>
      <li class="contact__item">
        <svg class="contact__icon" viewBox="0 0 24 24"><path d="M6.6 10.8a15 15 0 0 0 6.6 6.6l2.2-2.2a1 1 0 0 1 1-.25 11.4 11.4 0 0 0 3.6.57 1 1 0 0 1 1 1V20a1 1 0 0 1-1 1A17 17 0 0 1 3 4a1 1 0 0 1 1-1h3.5a1 1 0 0 1 1 1c0 1.25.2 2.45.57 3.57a1 1 0 0 1-.25 1z"/></svg>
        0170 555 47 12
      </li>
      <li class="contact__item">
        <svg class="contact__icon" viewBox="0 0 24 24"><circle cx="12" cy="12" r="10" fill="none" stroke="#ef8220" stroke-width="2.5"/><path d="M2 12h20M12 2c3 3 3 17 0 20M12 2c-3 3-3 17 0 20" fill="none" stroke="#ef8220" stroke-width="2"/></svg>
        www.tafelrunde-service.de
      </li>
      <li class="contact__item">
        <svg class="contact__icon" viewBox="0 0 24 24"><path d="M2 5h20v14H2z"/><path d="M2 5l10 8 10-8" fill="none" stroke="#272326" stroke-width="2"/></svg>
        info@tafelrunde-service.de
      </li>
      <li class="contact__item">
        <svg class="contact__icon" viewBox="0 0 24 24"><path d="M12 2a7 7 0 0 0-7 7c0 5 7 13 7 13s7-8 7-13a7 7 0 0 0-7-7zm0 9.5A2.5 2.5 0 1 1 12 6.5a2.5 2.5 0 0 1 0 5z"/></svg>
        Lindenweg 14, 45701 Musterstadt
      </li>
      <li class="contact__item">
        <svg class="contact__icon" viewBox="0 0 24 24"><rect x="2" y="2" width="20" height="20" rx="3"/></svg>
        www.social.example/tafelrundeservice
      </li>
    </ul>
  </div>

  <svg class="band" viewBox="0 0 700 40" preserveAspectRatio="none">
    <polygon points="0,32 520,10 520,40 0,40" fill="#ef8220"/>
    <polygon points="528,10 700,0 700,40 528,40" fill="#ffffff"/>
  </svg>
</section>

</body>
</html>
```